VitaBraid Web Design. Health and Wellness Industry

We are in process of creating next big Cloud based Health Care Management system. We have created 1st draft of Landing Page design. It is missing curb appeal, jazzy feel and engaging modern look.

Need a talented designer to recreate UI/ UX and take it to the next level.
If you are a creative designer, gifted with vision and imagination, I strongly encourage you to participate.

I want the designers to stay focus on the Landing page
Once we select the winner we will provide other subsequent pages
Follow up pages will be similar simple design

Target Market(s)

Individual Users and small business
Age Group 35-75
Individuals involved in "Health and Fitness" activity tracking, managing etc.

Industry/Entity Type

Health And Wellness

Number of Pages Required

5+ page

Colors
f68e4e
34a6d7

Requirements
Must have
• Super Engaging UI/ UX
• Smart and Contemporary look
• Easy to Navigate
• Folder Style menu bar
• Slideshow
• Social Medial Friendly
• Online Shopping
Nice to have
• Start from the enclosed draft Landing Page Idea.
• Feel Free to include additional frame, information section, Icon etc.

```html
<!DOCTYPE html>
<html lang="en">
<head>
<meta charset="utf-8">
<title>VitaBraid – Stay in Synk Round The Clock</title>
<link rel="stylesheet" href="https://fonts.googleapis.com/css2?family=Open+Sans:wght@300;400;600;700&display=swap">
<style>
:root{
  --orange:#f68e4e;
  --orange-dark:#e8753a;
  --blue:#34a6d7;
  --blue-dark:#2a86b3;
  --red:#e8443a;
  --ink:#3b3f45;
  --muted:#8a8f96;
  --line:#e2e4e7;
  --panel:#f1f2f4;
  --footer:#f4f4f5;
  --bar:#2f3338;
  --white:#ffffff;
}
*{box-sizing:border-box;margin:0;padding:0}
html,body{width:1200px;height:2244px;overflow:hidden}
body{font-family:"Open Sans",Arial,sans-serif;color:var(--ink);background:var(--white);position:relative;font-size:13px}
a{color:inherit;text-decoration:none}

/* header */
.site-header{height:64px;display:flex;align-items:center;justify-content:space-between;padding:0 40px}
.brand{display:flex;align-items:center;gap:10px;font-size:30px;font-weight:600;color:var(--orange);letter-spacing:-.5px}
.brand-dot{width:14px;height:14px;border-radius:50%;background:var(--orange)}
.header-tools{display:flex;align-items:center;gap:8px}
.search{width:170px;height:24px;border:1px solid var(--line);border-radius:2px;font-size:10px;color:var(--muted);padding:4px 8px;display:flex;justify-content:space-between;align-items:center}
.btn-sm{height:24px;padding:0 14px;border-radius:2px;color:var(--white);font-size:10px;font-weight:700;display:flex;align-items:center}
.btn-login{background:var(--orange)}
.btn-signup{background:var(--blue)}
.lang{width:22px;height:14px;background:var(--blue);border-radius:1px}

/* nav */
.main-nav{height:36px;border-top:1px solid var(--line);border-bottom:1px solid var(--line);display:flex;align-items:stretch;padding:0 40px;gap:4px}
.main-nav a{display:flex;align-items:center;gap:8px;padding:0 22px;font-size:11px;font-weight:600;color:var(--muted);text-transform:uppercase}
.main-nav a .ico{width:12px;height:12px;border-radius:50%;border:2px solid currentColor}
.main-nav a.active{background:var(--orange);color:var(--white)}
.main-nav .emergency{margin-left:auto;background:var(--red);color:var(--white)}

/* hero */
.hero{position:relative;height:430px;background:linear-gradient(90deg,#fafafa,#eef1f3)}
.hero-art{position:absolute;left:40px;top:10px;width:640px;height:420px;border-radius:0;
  background:radial-gradient(circle at 30% 70%,#f4a93a 0 20%,transparent 21%),
             radial-gradient(circle at 58% 62%,#e8443a 0 18%,transparent 19%),
             radial-gradient(circle at 78% 55%,#34a6d7 0 16%,transparent 17%),
             linear-gradient(135deg,#9fd0e4,#f6b07a 55%,#5b6d7a)}
.hero-copy{position:absolute;left:770px;top:170px}
.hero-copy h1{font-weight:300;font-size:38px;line-height:1.15;color:var(--ink)}
.hero-actions{display:flex;gap:12px;margin-top:22px}
.btn-outline{height:32px;padding:0 18px;border:2px solid var(--orange);border-radius:18px;font-size:11px;font-weight:700;color:var(--orange);display:flex;align-items:center}

/* tabs */
.section-tabs{position:absolute;top:542px;left:72px;width:1056px;height:42px;display:flex;border-bottom:1px solid var(--line)}
.section-tabs a{flex:1;display:flex;align-items:center;justify-content:center;font-size:11px;color:var(--muted);border-right:1px solid var(--line)}
.section-tabs a:last-child{border-right:0}
.section-tabs a.active{background:var(--orange);color:var(--white);font-weight:600}

/* feature panel */
.features{position:absolute;top:584px;left:72px;width:1056px;height:930px;background:var(--panel);display:flex;padding:0 0 24px 0}
.feature-list{width:228px;padding-top:20px}
.feature-list li{list-style:none;height:64px;display:flex;align-items:center;padding-left:20px;font-size:14px;color:var(--ink);border-bottom:1px solid var(--line)}
.feature-list li.active{background:var(--white)}
.feature-body{flex:1;background:var(--white);margin:20px 24px 0 0;padding:36px 40px;position:relative}
.feature-body h2{font-size:24px;font-weight:400;color:var(--ink)}
.access-card{width:260px;margin:36px auto 0;border:1px solid var(--line);box-shadow:0 6px 14px rgba(0,0,0,.12)}
.access-head{height:46px;background:linear-gradient(#3d4a58,#2c3742);display:flex;align-items:center;justify-content:center}
.access-head span{background:var(--blue);color:var(--white);font-weight:600;font-size:15px;padding:6px 22px;letter-spacing:1px}
.access-opt{height:44px;display:flex;align-items:center;gap:12px;padding-left:14px;font-size:10px;color:var(--muted);border-top:1px solid var(--line)}
.access-opt .radio{width:10px;height:10px;border-radius:50%;border:1px solid #b7bcc2}
.access-opt .glyph{width:18px;height:18px;border-radius:3px;background:#c6cbd1}
.access-opt.selected{background:#eef7fc;color:var(--blue-dark)}
.access-opt.selected .radio{background:var(--blue);border-color:var(--blue)}
.access-opt.selected .glyph{background:var(--blue)}
.feature-text{margin-top:40px;font-size:11px;line-height:1.65;color:var(--muted)}
.feature-text p{margin-bottom:14px}
.see-all{position:absolute;left:40px;bottom:24px;font-size:11px;color:var(--muted);display:flex;align-items:center;gap:6px}
.see-all i{width:10px;height:10px;border-radius:50%;border:1px solid var(--muted)}

/* get started */
.get-started{position:absolute;top:1556px;left:0;width:1200px}
.get-started h2{margin-left:72px;font-size:26px;font-weight:600;color:var(--ink)}
.steps{display:flex;justify-content:space-between;align-items:flex-start;margin:40px 72px 0}
.step{width:200px;text-align:center}
.step-icon{width:84px;height:84px;margin:0 auto}
.step h3{font-size:15px;font-weight:600;margin-top:24px}
.step p{font-size:11px;color:var(--muted);line-height:1.6;margin-top:10px}
.step-arrow{margin-top:30px}

/* footer */
.site-footer{position:absolute;top:1960px;left:0;width:1200px;height:240px;background:var(--footer);border-top:1px solid var(--line);display:flex;padding:36px 72px 0;gap:60px}
.foot-col h4{display:flex;align-items:center;gap:8px;font-size:13px;font-weight:600;margin-bottom:12px}
.foot-col h4 i{width:22px;height:22px;border-radius:50%;background:var(--orange)}
.foot-col li{list-style:none;font-size:10px;color:var(--muted);line-height:2;padding-left:30px}
.badges{margin-left:auto;display:flex;flex-direction:column;gap:12px}
.badge{width:150px;height:44px;border-radius:6px;background:#2b2e33}
.bottom-bar{position:absolute;top:2200px;left:0;width:1200px;height:44px;background:var(--bar);display:flex;align-items:center;justify-content:space-between;padding:0 72px;font-size:10px;color:#b7bcc2}
.social{display:flex;gap:8px}
.social span{width:22px;height:22px;border-radius:50%;background:var(--blue)}
.social span:nth-child(2){background:#5a6b7a}
.social span:nth-child(3){background:var(--orange)}
.social span:nth-child(4){background:var(--red)}
</style>
</head>
<body>

<header class="site-header">
  <a class="brand" href="#"><span class="brand-dot"></span>VitaBraid</a>
  <div class="header-tools">
    <div class="search">Search here<span>⌕</span></div>
    <a class="btn-sm btn-login" href="#">LOGIN</a>
    <a class="btn-sm btn-signup" href="#">SIGN UP</a>
    <span class="lang"></span>
  </div>
</header>

<nav class="main-nav">
  <a class="active" href="#"><span class="ico"></span>Home</a>
  <a href="#"><span class="ico"></span>WellVault</a>
  <a href="#"><span class="ico"></span>Products</a>
  <a href="#"><span class="ico"></span>VideoCare</a>
  <a href="#"><span class="ico"></span>Community</a>
  <a class="emergency" href="#"><span class="ico"></span>Emergency Login</a>
</nav>

<section class="hero">
  <div class="hero-art" role="img" aria-label="Colourful profile silhouettes with health icons: water drop, heart, medical kit and gears"></div>
  <div class="hero-copy">
    <h1>Stay in Synk<br>Round The Clock</h1>
    <div class="hero-actions">
      <a class="btn-outline" href="#">LEARN MORE</a>
      <a class="btn-outline" href="#">WATCH VIDEO</a>
    </div>
  </div>
</section>

<nav class="section-tabs">
  <a href="#">Overview</a>
  <a href="#">How it works</a>
  <a class="active" href="#">Data Synchronization</a>
  <a href="#">Medical Emergency</a>
  <a href="#">Stories</a>
  <a href="#">Get Started</a>
</nav>

<section class="features">
  <ul class="feature-list">
    <li>Data Synchronization</li>
    <li>Safe &amp; Secure WellVault</li>
    <li class="active">Control Your Content</li>
  </ul>
  <article class="feature-body">
    <h2>Control Your Content</h2>
    <div class="access-card">
      <div class="access-head"><span>ACCESS</span></div>
      <div class="access-opt"><span class="radio"></span><span class="glyph"></span>USERS</div>
      <div class="access-opt selected"><span class="radio"></span><span class="glyph"></span>YOUR COMPANY</div>
      <div class="access-opt"><span class="radio"></span><span class="glyph"></span>COLLABORATORS</div>
      <div class="access-opt"><span class="radio"></span><span class="glyph"></span>NO LINK</div>
    </div>
    <div class="feature-text">
      <p>Do you need to share highly confidential documents? Use the rich permission and reporting capabilities of the vault to get comprehensive control over every document in your business.</p>
      <p>Granular Permissions: Choose from seven different permission types, including "view" or "upload only", to control exactly who has access to which documents.</p>
      <p>WellVault Reports: Create secure business processes with features like email uploading, location-based access, content automation and strict security policies.</p>
      <p>No More Out-of-Date Files: Make sure your current version is available to users with a dedicated file deletion and full document history.</p>
    </div>
    <a class="see-all" href="#"><i></i>See all</a>
  </article>
</section>

<section class="get-started">
  <h2>Get Started</h2>
  <div class="steps">
    <div class="step">
      <svg class="step-icon" viewBox="0 0 84 84"><circle cx="42" cy="42" r="40" fill="none" stroke="#f68e4e" stroke-width="3"/><circle cx="42" cy="34" r="10" fill="none" stroke="#f68e4e" stroke-width="3"/><path d="M24 62c2-10 10-15 18-15s16 5 18 15" fill="none" stroke="#f68e4e" stroke-width="3"/></svg>
      <h3>Sign up Free</h3>
      <p>Lorem ipsum dolor sit amet, consectetur adipiscing elit, sed diam nonummy nibh euismod tincidunt ut laoreet dolore.</p>
    </div>
    <svg class="step-arrow" width="40" height="24" viewBox="0 0 40 24"><path d="M2 12h32M26 4l8 8-8 8" fill="none" stroke="#c6cbd1" stroke-width="3"/></svg>
    <div class="step">
      <svg class="step-icon" viewBox="0 0 84 84"><circle cx="36" cy="42" r="16" fill="none" stroke="#f68e4e" stroke-width="3"/><circle cx="36" cy="42" r="6" fill="#f68e4e"/><circle cx="62" cy="26" r="10" fill="none" stroke="#f68e4e" stroke-width="3"/><path d="M36 20v6M36 58v6M14 42h6M52 42h6" stroke="#f68e4e" stroke-width="4"/></svg>
      <h3>Complete Simple Setup</h3>
      <p>Lorem ipsum dolor sit amet, consectetur adipiscing elit, sed diam nonummy nibh euismod tincidunt ut laoreet dolore.</p>
    </div>
    <svg class="step-arrow" width="40" height="24" viewBox="0 0 40 24"><path d="M2 12h32M26 4l8 8-8 8" fill="none" stroke="#c6cbd1" stroke-width="3"/></svg>
    <div class="step">
      <svg class="step-icon" viewBox="0 0 84 84"><rect x="10" y="16" width="54" height="38" rx="3" fill="none" stroke="#f68e4e" stroke-width="3"/><path d="M28 66h20M38 54v12" stroke="#f68e4e" stroke-width="3"/><rect x="56" y="34" width="20" height="34" rx="3" fill="#fff" stroke="#f68e4e" stroke-width="3"/></svg>
      <h3>Select &amp; Connect Devices</h3>
      <p>Lorem ipsum dolor sit amet, consectetur adipiscing elit, sed diam nonummy nibh euismod tincidunt ut laoreet dolore.</p>
    </div>
    <svg class="step-arrow" width="40" height="24" viewBox="0 0 40 24"><path d="M2 12h32M26 4l8 8-8 8" fill="none" stroke="#c6cbd1" stroke-width="3"/></svg>
    <div class="step">
      <svg class="step-icon" viewBox="0 0 84 84"><rect x="22" y="10" width="40" height="64" rx="5" fill="none" stroke="#f68e4e" stroke-width="3"/><path d="M32 40a10 10 0 0 1 18-4M52 44a10 10 0 0 1-18 4" fill="none" stroke="#f68e4e" stroke-width="3"/><circle cx="42" cy="66" r="2.5" fill="#f68e4e"/></svg>
      <h3>Sync Your Data</h3>
      <p>Lorem ipsum dolor sit amet, consectetur adipiscing elit, sed diam nonummy nibh euismod tincidunt ut laoreet dolore.</p>
    </div>
  </div>
</section>

<footer class="site-footer">
  <div class="foot-col">
    <h4><i></i>Company</h4>
    <ul><li>About Us</li><li>The Buzz</li><li>Careers</li><li>Partners</li><li>Payment Options</li></ul>
  </div>
  <div class="foot-col">
    <h4><i></i>Products</h4>
    <ul><li>Blood Pressure Monitors</li><li>Wireless Scales</li><li>Pulse Oximeters</li><li>Glucometers</li><li>Store</li></ul>
  </div>
  <div class="foot-col">
    <h4><i></i>Contacts</h4>
    <ul><li>Support</li><li>Shipping/Returns</li><li>Contact Us</li><li>Investors</li><li>Tradeshows</li></ul>
  </div>
  <div class="foot-col">
    <h4><i></i>Downloads</h4>
    <ul><li>Mobile App</li><li>Device Driver</li><li>API</li><li>Paper Kit</li><li>Advertisement</li></ul>
  </div>
  <div class="badges">
    <span class="badge"></span>
    <span class="badge"></span>
  </div>
</footer>

<div class="bottom-bar">
  <span>Company Statement  |  Privacy Policy  |  Terms and Conditions<br>Copyright © 2015 VitaBraid – All Rights Reserved</span>
  <div class="social"><span></span><span></span><span></span><span></span><span></span></div>
</div>

</body>
</html>
```